We need a complete design for our construction company KELTO CONSTRUCTION based in Auckland New Zealand, we need a logo, website, business card, vehicle design etc..
We are a mid to high-end construction company who work mostly on residential projects and some commercial.

What we want to see in the design;
Professional,
Architectural,
Simple,
Alternative,

We want the design to communicate professionalism, high quality wormanship and and quality service.

Target Market(s)

People looking for a quality building/ construction company

Industry/Entity Type

Construction Company

Contact Information for Business Card

KELTO CONSTRUCTION.co.nz
Lino Verasek
lino@keltoconstruction.example.nz
021 5807 462

Logo Text

KELTO CONSTRUCTION

Number of Pages Required

5+ page

Font styles to use
Sans Serif

Colors

Designer to choose colors to be used in the design.

Requirements
Must have
• Must appear high end, professional, quality, be simple, easy to use, give security to potential clients
Nice to have
• high-quality photos of our recent projects
• about us page
• blog page
• contact us page
• high quality content
Should not have
• should not be hard to use and have too much going on.

```html
<!DOCTYPE html>
<html lang="en">
<head>
<meta charset="utf-8">
<title>Kelto Construction</title>
<link href="https://fonts.googleapis.com/css2?family=Montserrat:ital,wght@0,400;0,500;0,600;0,700;1,400&family=Roboto:wght@400;500;700&display=swap" rel="stylesheet">
<style>
:root{
  --orange:#e4550f;
  --ink:#1b1b1b;
  --dark:#151719;
  --muted:#6b6b6b;
  --light:#f5f5f5;
  --white:#ffffff;
  --footer:#000000;
  --rule:#1b1b1b;
}
*{box-sizing:border-box;margin:0;padding:0}
html,body{width:1200px;height:2970px;overflow:hidden}
body{position:relative;background:var(--white);font-family:"Montserrat",sans-serif;color:var(--ink)}
.abs{position:absolute}
.heading{font-family:"Roboto",sans-serif;font-weight:500;color:#2c2c2c;text-align:center;left:0;width:1200px}
.heading span{color:var(--orange)}
.divider{left:560px;width:80px;height:2px;background:var(--rule)}

/* header */
.site-header{left:0;top:0;width:1200px;height:120px;background:var(--white)}
.brand{left:86px;top:44px;display:flex;align-items:center;gap:10px}
.brand-mark{width:14px;height:14px;background:var(--orange)}
.brand-name{font-family:"Montserrat",sans-serif;font-weight:600;font-size:22px;color:var(--orange);letter-spacing:1px;line-height:1}
.topbar{right:88px;top:22px;font-size:14px;color:var(--orange);font-weight:500;display:flex;align-items:center;gap:10px}
.topbar svg{width:13px;height:13px;fill:var(--orange)}
.topbar .sep{margin:0 12px}
.nav{left:542px;top:68px;display:flex;gap:27px;font-size:14px;color:#222;font-weight:500}
.nav .active{color:var(--orange);position:relative}
.nav .active::after{content:"";position:absolute;left:-2px;right:-2px;bottom:-7px;height:2px;background:var(--orange)}
.quote-btn{left:967px;top:61px;width:145px;height:34px;background:var(--orange);color:var(--white);font-size:13px;font-weight:600;display:flex;align-items:center;justify-content:center}

/* hero */
.hero{left:0;top:120px;width:1200px;height:500px;background:linear-gradient(100deg,#1a1c1f 0%,#2a2d31 45%,#3b3f44 70%,#2b3038 100%)}
.hero-title{left:88px;top:125px;font-size:34px;line-height:48px;color:var(--white);font-weight:500}
.hero-text{left:88px;top:232px;width:640px;font-size:14px;line-height:25px;color:#e6e6e6}
.btn-solid,.btn-line{top:308px;height:46px;font-size:18px;font-weight:500;display:flex;align-items:center;justify-content:center;color:var(--white)}
.btn-solid{left:88px;width:193px;background:var(--orange)}
.btn-line{left:295px;width:190px;border:2px solid var(--white)}
.slider-tab{left:534px;top:472px;width:132px;height:28px;background:var(--white);border-radius:22px 22px 0 0}
.dots{display:flex;gap:4px;justify-content:center}
.dots i{width:14px;height:14px;border-radius:50%;border:1.5px solid #333;display:block}
.dots i.on{background:var(--orange);border-color:var(--orange)}

/* welcome */
.welcome-text{left:180px;top:778px;width:840px;text-align:center;font-size:15.5px;line-height:26px;color:#222}
.small-btn{background:var(--orange);color:var(--white);font-size:13px;font-weight:600;display:flex;align-items:center;justify-content:center}

/* offers */
.offer{top:1020px;height:478px;color:var(--white)}
.offer-res{left:0;width:598px;background:linear-gradient(160deg,#2c3035 0%,#1a1c1f 60%,#111214 100%)}
.offer-com{left:604px;width:596px;background:linear-gradient(160deg,#e8661f 0%,#e4550f 55%,#d44c0b 100%)}
.offer-in{left:86px;top:108px;width:400px}
.offer-kicker{font-size:21px}
.offer-title{font-size:49px;line-height:60px;margin-top:4px}
.offer-rule{width:145px;height:3px;margin:10px 0 16px}
.offer-res .offer-rule{background:var(--orange)}
.offer-com .offer-rule{background:var(--white)}
.offer-text{font-size:13.5px;line-height:20.5px}
.offer-more{font-size:13.5px;margin-top:20px}
.offer-res .offer-more{color:var(--orange)}

/* projects */
.projects-text{left:210px;top:1648px;width:780px;text-align:center;font-size:15.5px;line-height:26px;color:#222}
.filter{top:1716px;height:34px;font-size:13px;font-weight:600;color:var(--white);display:flex;align-items:center;justify-content:center}
.filter-on{background:var(--orange)}
.filter-off{background:#111}
.tile{display:block}
.tile-title{display:flex;align-items:center;justify-content:center;color:var(--orange);font-size:19px;font-weight:500}

/* testimonial */
.testimonials{left:0;top:2305px;width:1200px;height:355px;background:var(--light)}
.quote{left:0;top:2440px;width:1200px;text-align:center;font-style:italic;font-size:22px;line-height:36px;color:#6f6f6f}
.author{left:0;top:2532px;width:1200px;text-align:center;font-size:22px;color:var(--orange)}

/* footer */
.site-footer{left:0;top:2660px;width:1200px;height:310px;background:var(--footer);color:var(--white)}
.foot-head{font-size:16px;color:var(--orange);font-weight:500}
.foot-row{display:flex;gap:16px;font-size:14.5px;line-height:26px;font-weight:500}
.foot-row svg{width:14px;height:14px;fill:var(--orange);margin-top:6px;flex:none}
.vline{width:1px;background:#333;top:30px;height:160px}
.links{list-style:none;font-size:12.5px;line-height:25px;font-weight:500}
.links li::before{content:">";color:var(--orange);margin-right:16px}
.email-field{left:842px;top:78px;width:272px;height:50px;border:1.5px solid #ddd;font-size:12.5px;color:#999;padding-left:20px;display:flex;align-items:center}
.submit{left:840px;top:136px;width:193px;height:46px;background:var(--orange);font-size:18px;font-weight:600;letter-spacing:1px;display:flex;align-items:center;justify-content:center}
.hline{left:86px;top:215px;width:1028px;height:1px;background:#333}
.copyright{left:86px;top:246px;font-size:13px;font-weight:500;color:#ddd}
.social{left:893px;top:238px;display:flex;gap:12px}
.social i{width:34px;height:34px;border-radius:50%;display:block}
</style>
</head>
<body>

<header class="abs site-header">
  <div class="abs brand">
    <span class="brand-mark"></span>
    <span class="brand-name">KELTO CONSTRUCTION</span>
  </div>
  <div class="abs topbar">
    <svg viewBox="0 0 24 24"><path d="M6.6 10.8a15.1 15.1 0 0 0 6.6 6.6l2.2-2.2c.3-.3.7-.4 1-.2 1.1.4 2.3.6 3.6.6.6 0 1 .4 1 1V20c0 .6-.4 1-1 1C10.6 21 3 13.4 3 4c0-.6.4-1 1-1h3.5c.6 0 1 .4 1 1 0 1.3.2 2.5.6 3.6.1.3 0 .7-.2 1z"/></svg>
    <span>0123 987 6540</span>
    <span class="sep">|</span>
    <svg viewBox="0 0 24 24"><path d="M2 5h20v14H2z"/><path d="M3 6l9 7 9-7" stroke="#fff" stroke-width="1.6" fill="none"/></svg>
    <span>info@keltoconstruction.example.nz</span>
  </div>
  <nav class="abs nav">
    <span class="active">Home</span><span>About us</span><span>Projects</span><span>Blog</span><span>Contact us</span>
  </nav>
  <div class="abs quote-btn">Get a free Quote</div>
</header>

<section class="abs hero" role="img" aria-label="Dusky city construction site with a worker in a hi-vis vest holding a yellow hard hat">
  <h1 class="abs hero-title">Kelto Construction is a<br>Mid to High-End construction company.</h1>
  <p class="abs hero-text">Lorem Ipsum is simply dummy text of the printing and typesetting industry. Lorem Ipsum has been the industry's standard dummy text ever since the 1500s.</p>
  <div class="abs btn-solid">Residential</div>
  <div class="abs btn-line">Commercial</div>
  <div class="abs slider-tab"><div class="dots" style="margin-top:9px"><i></i><i></i><i class="on"></i><i></i><i></i></div></div>
</section>

<section class="welcome">
  <h2 class="abs heading" style="top:690px;font-size:35px">Welcome to <span>Kelto Construction</span></h2>
  <div class="abs divider" style="top:754px"></div>
  <p class="abs welcome-text">Lorem Ipsum is simply dummy text of the printing and typesetting industry. Lorem Ipsum has been the industry's standard dummy text ever since the 1500s, when an unknown printer took a galley of type and scrambled it to make a type specimen book. It has survived not only five centuries, but also the leap into electronic typesetting, remaining essentially unchanged.</p>
  <div class="abs small-btn" style="left:524px;top:907px;width:154px;height:34px">Learn More Kelto</div>
</section>

<section class="abs offer offer-res" role="img" aria-label="Modern residential house at dusk reflected in a pool">
  <div class="abs offer-in">
    <div class="offer-kicker">We Offer</div>
    <div class="offer-title">Residential</div>
    <div class="offer-rule"></div>
    <p class="offer-text">Lorem Ipsum is simply dummy text of the printing and typesetting industry. Lorem Ipsum has been the industry's standard dummy text ever since the 1500s, when an unknown printer took a galley of type and scrambled it to make a type specimen book.</p>
    <div class="offer-more">Read More &gt;</div>
  </div>
</section>
<section class="abs offer offer-com" role="img" aria-label="Commercial tower cranes over a building site, orange tinted">
  <div class="abs offer-in">
    <div class="offer-kicker">We Offer</div>
    <div class="offer-title">Commercial</div>
    <div class="offer-rule"></div>
    <p class="offer-text">Lorem Ipsum is simply dummy text of the printing and typesetting industry. Lorem Ipsum has been the industry's standard dummy text ever since the 1500s, when an unknown printer took a galley of type and scrambled it to make a type specimen book.</p>
    <div class="offer-more">Read More &gt;</div>
  </div>
</section>

<section class="projects">
  <h2 class="abs heading" style="top:1563px;font-size:34px">Kelto <span>Recent projects</span></h2>
  <div class="abs divider" style="top:1624px"></div>
  <p class="abs projects-text">Lorem Ipsum is simply dummy text of the printing and typesetting industry. Lorem Ipsum has been the industry's standard dummy text ever since the 1500s,</p>
  <div class="abs filter filter-on" style="left:444px;width:56px">All</div>
  <div class="abs filter filter-off" style="left:514px;width:120px">Residential</div>
  <div class="abs filter filter-off" style="left:638px;width:118px">Commercial</div>

  <div class="abs tile" style="left:87px;top:1788px;width:295px;height:210px;background:linear-gradient(180deg,#2d5a9a 0%,#4a6a8c 55%,#6a5a40 80%,#3b5a2a 100%)" role="img" aria-label="Lit two-storey family home at blue hour"></div>
  <div class="abs tile" style="left:405px;top:1788px;width:391px;height:442px;background:linear-gradient(180deg,#c9b48a 0%,#8f8a7c 45%,#4f5a60 100%)" role="img" aria-label="High-rise towers under construction with cranes"></div>
  <div class="abs tile" style="left:818px;top:1788px;width:294px;height:210px;background:linear-gradient(180deg,#1e3550 0%,#3e4650 55%,#6a5536 85%,#3e4a2e 100%)" role="img" aria-label="Modern home with lit windows at dusk"></div>
  <div class="abs tile tile-title" style="left:87px;top:2020px;width:295px;height:210px;background:linear-gradient(180deg,#2a2c2f 0%,#1a1b1d 100%)" role="img" aria-label="Dark project image with overlay title">Title Goes Here</div>
  <div class="abs tile" style="left:818px;top:2020px;width:294px;height:210px;background:linear-gradient(180deg,#8aa3bf 0%,#9a8270 50%,#b0926a 100%)" role="img" aria-label="House timber framing on a site with sand piles"></div>
</section>

<section class="abs testimonials">
  <h2 class="abs heading" style="top:53px;font-size:35px">Our Thousand of <span>Happy Customer</span></h2>
  <div class="abs divider" style="top:114px"></div>
</section>
<p class="abs quote">“Lorem Ipsum is simply dummy text of the printing and typesetting industry.<br>Lorem Ipsum has been the industry's standard dummy text”</p>
<p class="abs author">- Mara T Ellison</p>
<div class="abs dots" style="left:0;top:2585px;width:1200px"><i></i><i></i><i class="on"></i><i></i><i></i></div>

<footer class="abs site-footer">
  <div class="abs foot-head" style="left:86px;top:38px">Contact Info:</div>
  <div class="abs" style="left:86px;top:70px">
    <div class="foot-row"><svg viewBox="0 0 24 24"><path d="M12 2a7 7 0 0 0-7 7c0 5 7 13 7 13s7-8 7-13a7 7 0 0 0-7-7zm0 9.5A2.5 2.5 0 1 1 12 6.5a2.5 2.5 0 0 1 0 5z"/></svg><div>Kelto Construction<br>48 Harlow Street, Auckland, 1022.</div></div>
    <div class="foot-row" style="margin-top:10px"><svg viewBox="0 0 24 24"><path d="M6.6 10.8a15.1 15.1 0 0 0 6.6 6.6l2.2-2.2c.3-.3.7-.4 1-.2 1.1.4 2.3.6 3.6.6.6 0 1 .4 1 1V20c0 .6-.4 1-1 1C10.6 21 3 13.4 3 4c0-.6.4-1 1-1h3.5c.6 0 1 .4 1 1 0 1.3.2 2.5.6 3.6.1.3 0 .7-.2 1z"/></svg><div>Tel: +0123 987 6540</div></div>
    <div class="foot-row" style="margin-top:10px"><svg viewBox="0 0 24 24"><path d="M2 5h20v14H2z"/><path d="M3 6l9 7 9-7" stroke="#000" stroke-width="1.6" fill="none"/></svg><div>Mail: info@keltoconstruction.example.nz</div></div>
  </div>
  <div class="abs vline" style="left:462px"></div>
  <div class="abs foot-head" style="left:563px;top:38px">Quick Links:</div>
  <ul class="abs links" style="left:563px;top:67px">
    <li>Home</li><li>About us</li><li>Projects</li><li>Blog</li><li>Contact us</li>
  </ul>
  <div class="abs vline" style="left:755px"></div>
  <div class="abs foot-head" style="left:840px;top:38px">Newsletter Signup</div>
  <div class="abs email-field">Email Address</div>
  <div class="abs submit">SUBMIT</div>
  <div class="abs hline"></div>
  <div class="abs copyright">Copyright © 2018. Kelto Construction. All rights reserved.</div>
  <div class="abs social" aria-label="Social media links">
    <i style="background:#3b5a9a"></i><i style="background:#3aa0e0"></i><i style="background:#d84a38"></i><i style="background:#d8281e"></i><i style="background:#b0388a"></i>
  </div>
</footer>

</body>
</html>
```